Verodex business card

Business card for sustainable investment company called "Verodex". Verodex is an exchange platform selling carbon credits between buyers and sellers. Carbon Credits are an environmental commodity for reducing global carbon emissions.

the card should obviously have our logo and the theme should be sustainability/environment mixed with a trading platform.

Contact Information for Business Card

Logo, Name, Title, Phone, Email

Colors
0054AA
0677BA
7BADD7
CADEEF
E8F1F8
0094D4
00A9DD
6FCCEA
C7EBF8
E9F6FB
00AB8E
00BBA5
67D7C9
C6EFE9
E9F9F6
59FF00
82FF00
B8FF75
E3FFCB
F4FFEA

```html
<!DOCTYPE html>
<html lang="en">
<head>
<meta charset="UTF-8">
<title>Verodex Business Card</title>
<link rel="stylesheet" href="https://fonts.googleapis.com/css2?family=Montserrat:wght@400;600;700&display=swap">
<style>
  :root {
    --canvas-bg: #2b2c2e;
    --navy: #1c2b45;
    --brand-blue: #0677BA;
    --brand-deep: #0054AA;
    --brand-sky: #00A9DD;
    --brand-aqua: #6FCCEA;
    --card-white: #ffffff;
    --card-mist: #eef0f3;
    --rule: #2f3d5a;
    --muted: #3a4658;
  }
  * { margin: 0; padding: 0; box-sizing: border-box; }
  html, body {
    width: 1200px;
    height: 900px;
    overflow: hidden;
    background: var(--canvas-bg);
    font-family: "Montserrat", sans-serif;
  }
  .stage {
    position: relative;
    width: 1200px;
    height: 900px;
  }
  .card {
    position: absolute;
    left: 320px;
    width: 560px;
    height: 320px;
    border-radius: 26px;
    overflow: hidden;
    box-shadow: 0 14px 30px rgba(0,0,0,0.45);
  }
  .card--front {
    top: 110px;
    background: linear-gradient(20deg, var(--brand-aqua) 0%, #4aa8cc 35%, #3f8dc6 65%, #3f7fc6 100%);
    display: flex;
    align-items: center;
    justify-content: center;
  }
  .card--back {
    top: 470px;
    background: linear-gradient(160deg, var(--card-white) 0%, var(--card-mist) 100%);
  }
  .brand {
    display: flex;
    align-items: center;
    gap: 16px;
  }
  .brand__dot {
    width: 40px;
    height: 40px;
    border-radius: 50%;
  }
  .brand__name {
    font-weight: 600;
    font-size: 42px;
    letter-spacing: 2px;
  }
  .card--front .brand__dot { background: var(--card-white); }
  .card--front .brand__name { color: var(--card-white); }
  .card--back .brand {
    position: absolute;
    top: 58px;
    left: 0;
    right: 0;
    justify-content: center;
  }
  .card--back .brand__dot { background: var(--brand-blue); }
  .card--back .brand__name { color: var(--navy); }
  .person {
    position: absolute;
    top: 140px;
    left: 40px;
    right: 40px;
    display: flex;
    align-items: center;
    gap: 14px;
  }
  .person__rule {
    flex: 1;
    height: 1px;
    background: var(--rule);
  }
  .person__text { text-align: center; }
  .person__name {
    font-weight: 700;
    font-size: 17px;
    color: var(--navy);
    letter-spacing: 0.5px;
  }
  .person__title {
    font-weight: 400;
    font-size: 15px;
    color: var(--muted);
  }
  .contact {
    position: absolute;
    top: 212px;
    left: 0;
    right: 0;
    display: flex;
    flex-direction: column;
    align-items: center;
    gap: 8px;
  }
  .contact__item {
    display: flex;
    align-items: center;
    gap: 10px;
    font-size: 17px;
    color: var(--muted);
  }
  .contact__icon { width: 18px; height: 18px; }
</style>
</head>
<body>
<main class="stage">
  <section class="card card--front" aria-label="Card front">
    <div class="brand">
      <span class="brand__dot"></span>
      <span class="brand__name">VERODEX</span>
    </div>
  </section>

  <section class="card card--back" aria-label="Card back">
    <div class="brand">
      <span class="brand__dot"></span>
      <span class="brand__name">VERODEX</span>
    </div>
    <div class="person">
      <span class="person__rule"></span>
      <div class="person__text">
        <div class="person__name">DANIEL HARTE</div>
        <div class="person__title">Director</div>
      </div>
      <span class="person__rule"></span>
    </div>
    <div class="contact">
      <div class="contact__item">
        <svg class="contact__icon" viewBox="0 0 24 24" aria-hidden="true">
          <path fill="#0094D4" d="M6.6 10.8c1.4 2.8 3.8 5.1 6.6 6.6l2.2-2.2c.3-.3.7-.4 1-.2 1.1.4 2.3.6 3.6.6.6 0 1 .4 1 1V20c0 .6-.4 1-1 1C10.6 21 3 13.4 3 4c0-.6.4-1 1-1h3.5c.6 0 1 .4 1 1 0 1.3.2 2.5.6 3.6.1.3 0 .7-.2 1l-2.3 2.2z"/>
        </svg>
        <span>415-382-7160</span>
      </div>
      <div class="contact__item">
        <svg class="contact__icon" viewBox="0 0 24 24" aria-hidden="true">
          <rect x="2" y="5" width="20" height="14" rx="2" fill="#0094D4"/>
          <path d="M3 6l9 7 9-7" fill="none" stroke="#ffffff" stroke-width="1.6"/>
        </svg>
        <span>info@verodex.com</span>
      </div>
    </div>
  </section>
</main>
</body>
</html>
```